Website for "Bright Morrow Ltd" cleaning bsuiness

We require a website to expose our business to the local market. We want to provide background on who we are and what we do but in an easily digestible way. We clean domestic and commercial premises and want to provide a list of all of our services to potential customers. We operate out of Warrington in the UK.

We would like the website to be animated in some way so that the experience of using it is not dull or mundane. This website needs to be an extension of our company.

Target Market(s)

30 - 60 year olds for Domestic plus commercial clients

Industry/Entity Type

Cleaning Service

Coding

Coded - Design and coding required

Number of Pages Required

4 page

Font styles to use
Sans Serif

Colors
0455a3
3176b5
85acd3
cfdeed
ffffff
000000
1b1b1b
c8c8c8
757575

Requirements
Must have
• Logo which has been provided. Theme based around the logo and its colours. Simple layout to avoid confusion.
Nice to have
• Animations where possible to impress the customer.
Should not have
• any pictures of cleaning equipment, fairies, maids etc

```html
<!DOCTYPE html>
<html lang="en">
<head>
<meta charset="utf-8">
<title>Bright Morrow Ltd — Clean Domestic and Commercial</title>
<link rel="stylesheet" href="https://fonts.googleapis.com/css2?family=Roboto:wght@400;500;700&family=Oswald:wght@400;500&display=swap">
<style>
  :root {
    --brand: #3176b5;
    --brand-deep: #0455a3;
    --brand-soft: #85acd3;
    --brand-pale: #cfdeed;
    --white: #ffffff;
    --black: #000000;
    --ink: #1b1b1b;
    --line: #c8c8c8;
    --muted: #757575;
    --text: #444444;
    --panel: #f0f0f0;
    --footer: #333333;
    --footer-base: #1f1f1f;
  }
  * { box-sizing: border-box; margin: 0; padding: 0; }
  html, body { width: 1200px; height: 2575px; overflow: hidden; }
  body { font-family: "Roboto", Arial, sans-serif; color: var(--text); background: var(--white); position: relative; }
  .wrap { position: relative; width: 1020px; margin: 0 auto; }

  /* Header */
  .site-header { position: relative; height: 144px; background: var(--white); box-shadow: 0 1px 4px rgba(0,0,0,.12); z-index: 2; }
  .topbar { position: absolute; right: 0; top: 0; width: 770px; height: 38px; background: var(--brand); clip-path: polygon(28px 0, 100% 0, 100% 100%, 0 100%); color: var(--white); font-size: 14px; display: flex; align-items: center; }
  .topbar .contact { margin-left: 52px; display: flex; align-items: center; gap: 8px; }
  .topbar .contact svg { width: 13px; height: 13px; fill: var(--white); }
  .topbar .sep { margin: 0 6px; }
  .topbar .social { margin-left: auto; margin-right: 92px; display: flex; gap: 8px; }
  .topbar .social span { width: 14px; height: 14px; background: var(--white); border-radius: 2px; }
  .brand { position: absolute; left: 90px; top: 56px; display: flex; align-items: center; gap: 10px; }
  .brand .mark { width: 30px; height: 30px; border-radius: 50%; background: var(--brand-deep); }
  .brand .name { font-size: 28px; font-weight: 700; color: var(--brand-deep); letter-spacing: -.3px; }
  .main-nav { position: absolute; right: 88px; top: 88px; display: flex; gap: 46px; font-size: 15px; font-weight: 500; color: var(--ink); }
  .main-nav .active { color: var(--brand); }

  /* Hero */
  .hero { position: relative; height: 529px; overflow: hidden; }
  .hero .photo { position: absolute; inset: 0; background: linear-gradient(160deg, #d7dde4 0%, #eef1f4 35%, #b9c3cc 70%, #8a96a2 100%); }
  .hero .arrow { position: absolute; top: 380px; width: 34px; height: 34px; border-radius: 50%; background: rgba(30,30,30,.75); display: flex; align-items: center; justify-content: center; }
  .hero .arrow svg { width: 14px; height: 14px; stroke: var(--white); stroke-width: 2.5; fill: none; }
  .hero .prev { left: 53px; }
  .hero .next { right: 49px; }
  .hero .caption { position: absolute; right: 132px; top: 350px; text-align: right; color: var(--white); font-family: "Oswald", "Arial Narrow", sans-serif; text-shadow: 0 2px 6px rgba(0,0,0,.35); animation: rise 1.2s ease-out both; }
  .hero .caption h1 { font-size: 48px; font-weight: 500; line-height: 1.1; letter-spacing: .5px; }
  .hero .caption p { font-size: 31px; font-weight: 400; line-height: 1.2; }
  @keyframes rise { from { opacity: 0; transform: translateY(24px); } to { opacity: 1; transform: none; } }

  /* Intro blocks */
  .split { position: relative; }
  .split h2 { font-size: 27px; font-weight: 500; color: var(--ink); letter-spacing: .3px; }
  .split p { margin-top: 20px; font-size: 12.4px; line-height: 22.5px; text-align: justify; color: var(--text); }
  .btn { display: inline-block; margin-top: 26px; background: var(--brand); color: var(--white); font-size: 12.5px; font-weight: 500; padding: 0 20px; height: 34px; line-height: 34px; border-radius: 17px; transition: background .3s; }
  .btn:hover { background: var(--brand-deep); }
  .framed { position: absolute; background: var(--white); border: 1px solid #dcdcdc; box-shadow: 0 0 6px rgba(0,0,0,.12); padding: 6px; }
  .framed .photo { width: 100%; height: 100%; }

  .who { height: 405px; }
  .who .copy { position: absolute; left: 0; top: 78px; width: 520px; }
  .who .framed { left: 554px; top: 60px; width: 472px; height: 277px; }
  .who .photo { background: linear-gradient(135deg, #c9b9a0 0%, #e8e0d3 40%, #8b5a36 75%, #5b3a24 100%); }

  /* Services */
  .services { position: relative; height: 519px; overflow: hidden; }
  .services .backdrop { position: absolute; inset: 0; background: linear-gradient(180deg, #3a7dbd 0%, #2a6bae 45%, #1e5fa5 100%); }
  .services .inner { position: relative; padding-top: 66px; text-align: center; color: var(--white); }
  .services h2 { font-size: 29px; font-weight: 500; letter-spacing: .5px; }
  .services .lead { margin-top: 12px; font-size: 14.5px; }
  .service-grid { display: flex; gap: 9px; margin-top: 34px; }
  .service-card { width: 248px; height: 268px; background: var(--white); transition: transform .3s; }
  .service-card:hover { transform: translateY(-6px); }
  .service-card .photo { height: 215px; }
  .service-card h3 { height: 53px; line-height: 53px; font-size: 14.5px; font-weight: 500; color: var(--ink); letter-spacing: .3px; }
  .tone-a { background: linear-gradient(160deg, #f4f4f4, #cfd3d6 60%, #9a9fa3); }
  .tone-b { background: linear-gradient(160deg, #6b3b22, #a9794f 50%, #c9cfd4); }
  .tone-c { background: linear-gradient(160deg, #d9d3c8, #b68a5e 60%, #7a4b2b); }
  .tone-d { background: linear-gradient(160deg, #2c3d4e, #a7b7c5 50%, #e9eef2); }

  .what { height: 398px; }
  .what .framed { left: 0; top: 70px; width: 472px; height: 275px; }
  .what .photo { background: linear-gradient(135deg, #eae6df 0%, #cdbfae 40%, #a0583a 75%, #6e3420 100%); }
  .what .copy { position: absolute; left: 504px; top: 92px; width: 516px; }

  /* Blog */
  .blog { position: relative; height: 289px; background: var(--panel); }
  .blog .heading { position: absolute; left: 0; top: 46px; font-size: 21px; font-weight: 400; color: var(--ink); letter-spacing: .3px; }
  .blog .heading span { color: var(--brand); }
  .blog .pager { position: absolute; right: 8px; top: 50px; display: flex; gap: 4px; }
  .blog .pager svg { width: 10px; height: 14px; stroke: var(--ink); stroke-width: 2; fill: none; }
  .post { position: absolute; top: 96px; width: 500px; display: flex; gap: 14px; }
  .post.one { left: 0; }
  .post.two { left: 540px; top: 90px; }
  .post .photo { width: 162px; height: 143px; flex: none; }
  .post.two .photo { height: 143px; }
  .post h4 { font-size: 14.5px; font-weight: 400; color: #333; margin-top: 6px; }
  .post .date { margin-top: 6px; font-size: 12px; color: var(--brand); }
  .post p { margin-top: 6px; font-size: 11px; line-height: 19px; color: var(--text); }
  .post .more { margin-top: 6px; font-size: 11.5px; color: var(--brand); }
  .tone-e { background: linear-gradient(135deg, #e9e6e1, #c9c3bb 60%, #8f8a84); }
  .tone-f { background: linear-gradient(135deg, #cfd7de, #eef1f4 50%, #9aa6b1); }

  /* Footer */
  .site-footer { position: relative; height: 203px; background: var(--footer); color: var(--white); }
  .site-footer .col { position: absolute; top: 40px; }
  .site-footer h5 { font-size: 15px; font-weight: 500; letter-spacing: .3px; }
  .site-footer ul { list-style: none; margin-top: 22px; font-size: 11px; line-height: 24px; color: #e6e6e6; }
  .site-footer li::before { content: ""; display: inline-block; margin-right: 6px; border-left: 4px solid #e6e6e6; border-top: 3px solid transparent; border-bottom: 3px solid transparent; }
  .site-footer .col p { margin-top: 22px; font-size: 11px; line-height: 18.5px; color: #e6e6e6; }
  .col.links { left: 12px; }
  .col.areas { left: 210px; width: 225px; }
  .col.areas p { font-weight: 500; text-align: justify; }
  .col.touch { left: 546px; }
  .col.touch p { line-height: 22.5px; }
  .col.news { left: 808px; width: 212px; }
  .signup { margin-top: 16px; display: flex; height: 28px; }
  .signup .field { width: 145px; background: var(--white); color: var(--muted); font-size: 10px; line-height: 28px; padding-left: 14px; }
  .signup .send { width: 56px; background: var(--brand); color: var(--white); font-size: 12px; line-height: 28px; text-align: center; }

  .base { position: relative; height: 88px; background: var(--footer-base); color: var(--white); }
  .base .copy { position: absolute; left: 6px; top: 37px; font-size: 12px; }
  .base .social { position: absolute; right: 2px; top: 36px; display: flex; gap: 10px; }
  .base .social span { width: 15px; height: 15px; background: var(--white); border-radius: 2px; }
</style>
</head>
<body>

<header class="site-header">
  <div class="topbar">
    <div class="contact">
      <svg viewBox="0 0 24 24" aria-hidden="true"><path d="M6.6 10.8a15 15 0 0 0 6.6 6.6l2.2-2.2c.3-.3.7-.4 1-.2 1.1.4 2.3.6 3.6.6.6 0 1 .4 1 1V20c0 .6-.4 1-1 1A17 17 0 0 1 3 4c0-.6.4-1 1-1h3.5c.6 0 1 .4 1 1 0 1.3.2 2.5.6 3.6.1.3 0 .7-.2 1z"/></svg>
      <span>+44 1925 555 0148</span>
      <span class="sep">|</span>
      <svg viewBox="0 0 24 24" aria-hidden="true"><path d="M2 5h20v14H2z M2 5l10 8 10-8" fill="none" stroke="#fff" stroke-width="2"/></svg>
      <span>hello@brightmorrow.example</span>
    </div>
    <div class="social"><span></span><span></span><span></span><span></span></div>
  </div>
  <div class="brand"><span class="mark"></span><span class="name">Bright Morrow Ltd</span></div>
  <nav class="main-nav">
    <span class="active">HOME</span><span>ABOUT US</span><span>SERVICES</span><span>PROJECTS</span><span>FAQ</span><span>BLOG</span><span>CONTACT US</span>
  </nav>
</header>

<section class="hero">
  <div class="photo" role="img" aria-label="Bright modern glass hall with curved white ribs and a polished floor"></div>
  <span class="arrow prev"><svg viewBox="0 0 14 14"><path d="M9 2 4 7l5 5"/></svg></span>
  <span class="arrow next"><svg viewBox="0 0 14 14"><path d="M5 2l5 5-5 5"/></svg></span>
  <div class="caption">
    <h1>BRIGHT MORROW LTD</h1>
    <p>CLEAN DOMESTIC AND COMMERCIAL</p>
  </div>
</section>

<section class="split who wrap">
  <div class="copy">
    <h2>WHO WE ARE</h2>
    <p>Lorem Ipsum has been the industry's standard dummy text ever since the 1500s, when an unknown printer took a galley of type and scrambled it to make a type specimen book. It has survived not only five centuries, but also the leap into electronic typesetting, remaining essentially unchanged. It was popularised in the 1960s with the release of Lettrick sheets containing Lorem Ipsum passages, and more recently with desktop publishing software like Pagewright including versions of Lorem Ipsum.</p>
    <span class="btn">READ MORE</span>
  </div>
  <div class="framed"><div class="photo" role="img" aria-label="Sunlit open-plan kitchen with stone fireplace and wooden floor"></div></div>
</section>

<section class="services">
  <div class="backdrop" role="img" aria-label="Blue-toned spacious office interior"></div>
  <div class="inner wrap">
    <h2>SERVICES</h2>
    <p class="lead">Neque porro quisquam est qui dolorem ipsum quia dolor sit amet,</p>
    <div class="service-grid">
      <article class="service-card"><div class="photo tone-a" role="img" aria-label="White modern kitchen"></div><h3>CLEAN DOMESTIC</h3></article>
      <article class="service-card"><div class="photo tone-b" role="img" aria-label="Office lobby with wood panelling"></div><h3>CLEAN COMMERCIAL</h3></article>
      <article class="service-card"><div class="photo tone-c" role="img" aria-label="Dining room with herringbone floor"></div><h3>CLEAN DOMESTIC</h3></article>
      <article class="service-card"><div class="photo tone-d" role="img" aria-label="Glass corridor with gleaming floor"></div><h3>CLEAN COMMERCIAL</h3></article>
    </div>
  </div>
</section>

<section class="split what wrap">
  <div class="framed"><div class="photo" role="img" aria-label="Bright hallway and kitchen with polished wooden floor"></div></div>
  <div class="copy">
    <h2>WHAT WE DO</h2>
    <p>Lorem Ipsum has been the industry's standard dummy text ever since the 1500s, when an unknown printer took a galley of type and scrambled it to make a type specimen book. It has survived not only five centuries, but also the leap into electronic typesetting, remaining essentially unchanged. It was popularised in the 1960s with the release of Lettrick sheets containing Lorem Ipsum passages, and more recently with desktop publishing software like Pagewright including versions of Lorem Ipsum.</p>
    <span class="btn">READ MORE</span>
  </div>
</section>

<section class="blog">
  <div class="wrap" style="height:100%">
    <h2 class="heading">LATEST <span>BLOG</span></h2>
    <div class="pager"><svg viewBox="0 0 10 14"><path d="M8 2 3 7l5 5"/></svg><svg viewBox="0 0 10 14"><path d="M2 2l5 5-5 5"/></svg></div>
    <article class="post one">
      <div class="photo tone-e" role="img" aria-label="Cosy living room with sofa and rug"></div>
      <div>
        <h4>Nemo Enim Ipsam Volup</h4>
        <div class="date">09-07-2016</div>
        <p>Lorem Ipsum has been the industry's standard dummy text ever since the 1500s, when an unknown printer took a galley of type and scrambled it to make a type specimen book.</p>
        <div class="more">Read More &gt;&gt;</div>
      </div>
    </article>
    <article class="post two">
      <div class="photo tone-f" role="img" aria-label="Empty office with city view windows"></div>
      <div>
        <h4>Nemo Enim Ipsam Volup</h4>
        <div class="date">09-07-2016</div>
        <p>Lorem Ipsum has been the industry's standard dummy text ever since the 1500s, when an unknown printer took a galley of type and scrambled it to make a type specimen book.</p>
        <div class="more">Read More &gt;&gt;</div>
      </div>
    </article>
  </div>
</section>

<footer>
  <div class="site-footer">
    <div class="wrap" style="height:100%">
      <div class="col links">
        <h5>LINKS</h5>
        <ul><li>Customer Support</li><li>Documentation</li><li>Resources</li><li>General FAQs</li></ul>
      </div>
      <div class="col areas">
        <h5>CLEANING SERVICES</h5>
        <p>Lorem Ipsum has been the industry's standard dummy text ever since the 1500s, when an unknown printer took a galley of type and scrambled it to make a type specimen book.</p>
      </div>
      <div class="col touch">
        <h5>GET IN TOUCH</h5>
        <p>Address : 12 Larkfield Row,<br>Warrington, UK<br>Phone : 01925 555 0172<br>Email : hello@brightmorrow.example</p>
      </div>
      <div class="col news">
        <h5>NEWSLETTER</h5>
        <p>Your about us information would fit here nicely.</p>
        <div class="signup"><span class="field">Email address</span><span class="send">Submit</span></div>
      </div>
    </div>
  </div>
  <div class="base">
    <div class="wrap" style="height:100%">
      <span class="copy">Copyright © 2016. All Rights Reserved</span>
      <div class="social"><span></span><span></span><span></span><span></span></div>
    </div>
  </div>
</footer>

</body>
</html>
```